Modern Business Card For A Digital Advertising Company

I'll be print on the Pell Prints Velour paper http://us.pellprints.com/products/velour/business-cards.html
Need's to be modern and use the color palette of the logo or gray scales. I think integrating the pixelation of the logo in to the card and having it wrap from one side to the other could be interesting. My company provides ad operations, web development, and number of other services to websites around the world. You can see my website at http://www.zantorhq.com
Contact info on the card needs to have
Owen Lasko
President
p.318.204.6637
owen@zantorhq.com
http://www.zantorhq.com
Doesn't necessarily need to be in that order
Website owners
Business

```html
<!DOCTYPE html>
<html lang="en">
<head>
<meta charset="utf-8">
<title>Zantor HQ — Business Card</title>
<link rel="stylesheet" href="https://fonts.googleapis.com/css2?family=Open+Sans:wght@400;600;700&family=Questrial&display=swap">
<style>
  :root {
    --stage: #d9dadb;
    --paper: #ffffff;
    --green: #8dc63f;
    --green-dark: #6fa82a;
    --charcoal: #3d3f3c;
    --charcoal-deep: #2c2e2b;
    --ink: #4a4a4a;
    --white: #ffffff;
  }
  * { margin: 0; padding: 0; box-sizing: border-box; }
  html, body { width: 1200px; height: 450px; overflow: hidden; }
  body {
    background: var(--stage);
    position: relative;
    font-family: "Open Sans", Arial, sans-serif;
  }
  .card {
    position: absolute;
    top: 78px;
    width: 526px;
    height: 300px;
    overflow: hidden;
  }
  .card--front { left: 57px; background: var(--paper); }
  .card--back {
    left: 622px;
    background: linear-gradient(90deg, var(--charcoal) 0%, #474946 55%, var(--charcoal-deep) 100%);
  }

  /* Front */
  .brand {
    position: absolute;
    left: 60px;
    top: 150px;
    display: flex;
    align-items: center;
    gap: 10px;
  }
  .brand__mark { width: 22px; height: 22px; background: var(--green); }
  .brand__name {
    font-family: "Open Sans", Arial, sans-serif;
    font-weight: 700;
    font-size: 30px;
    letter-spacing: 1px;
    color: var(--green);
    line-height: 1;
  }
  .contact {
    position: absolute;
    left: 278px;
    top: 94px;
    list-style: none;
  }
  .contact__item {
    display: flex;
    align-items: center;
    gap: 6px;
    height: 22px;
    font-size: 14.5px;
    color: var(--ink);
  }
  .contact__icon { width: 11px; height: 11px; flex: none; }
  .swoosh { position: absolute; left: 0; bottom: 0; width: 526px; height: 300px; }
  .signature {
    position: absolute;
    left: 290px;
    top: 266px;
    color: var(--white);
    white-space: nowrap;
  }
  .signature__name { font-weight: 600; font-size: 18px; }
  .signature__title { font-size: 15px; }

  /* Back */
  .back-brand {
    position: absolute;
    left: 0; right: 0;
    top: 108px;
    display: flex;
    justify-content: center;
    align-items: center;
    gap: 16px;
  }
  .back-brand__mark { width: 40px; height: 40px; background: var(--white); }
  .back-brand__name {
    font-weight: 700;
    font-size: 54px;
    letter-spacing: 2px;
    color: var(--white);
    line-height: 1;
  }
  .back-url {
    position: absolute;
    left: 0; right: 0;
    top: 240px;
    text-align: center;
    font-family: "Questrial", "Open Sans", sans-serif;
    font-size: 20px;
    letter-spacing: 1.5px;
    color: var(--white);
  }
</style>
</head>
<body>
  <section class="card card--front" aria-label="Card front">
    <div class="brand">
      <span class="brand__mark"></span>
      <span class="brand__name">ZANTOR HQ</span>
    </div>

    <ul class="contact">
      <li class="contact__item">
        <svg class="contact__icon" viewBox="0 0 12 12" aria-hidden="true">
          <circle cx="6" cy="6" r="5.5" fill="none" stroke="var(--green)" stroke-width="1.2"/>
          <path d="M4 3.2 L5.2 4.6 L4.6 5.4 Q5.5 7 6.8 7.6 L7.6 7 L8.8 8.2 L8 9 Q5 8.6 3.3 4 Z" fill="var(--green)"/>
        </svg>
        <span>318.204.6637</span>
      </li>
      <li class="contact__item">
        <svg class="contact__icon" viewBox="0 0 12 12" aria-hidden="true">
          <circle cx="6" cy="6" r="6" fill="var(--green)"/>
          <rect x="3" y="4" width="6" height="4.2" fill="none" stroke="#fff" stroke-width="0.9"/>
          <path d="M3 4 L6 6.4 L9 4" fill="none" stroke="#fff" stroke-width="0.9"/>
        </svg>
        <span>owen@zantorhq.com</span>
      </li>
      <li class="contact__item">
        <svg class="contact__icon" viewBox="0 0 12 12" aria-hidden="true">
          <circle cx="6" cy="6" r="6" fill="var(--green)"/>
          <path d="M1 6 H11 M6 1 V11 M2 3.6 H10 M2 8.4 H10" stroke="#fff" stroke-width="0.8"/>
        </svg>
        <span>www.zantorhq.com</span>
      </li>
    </ul>

    <svg class="swoosh" viewBox="0 0 526 300" aria-hidden="true">
      <path d="M0 228 C150 200 330 212 470 248" fill="none" stroke="var(--charcoal)" stroke-width="5"/>
      <path d="M0 300 L0 270 C130 250 300 232 526 258 L526 300 Z" fill="var(--charcoal)"/>
      <path d="M0 248 C140 212 320 222 526 258 C320 238 140 242 0 262 Z" fill="var(--green)"/>
      <path d="M0 262 C140 242 320 238 526 258 C320 244 140 252 0 270 Z" fill="var(--paper)"/>
    </svg>

    <p class="signature">
      <span class="signature__name">Owen Lasko,</span>
      <span class="signature__title">President</span>
    </p>
  </section>

  <section class="card card--back" aria-label="Card back">
    <div class="back-brand">
      <span class="back-brand__mark"></span>
      <span class="back-brand__name">ZANTOR HQ</span>
    </div>
    <p class="back-url">www.zantorhq.com</p>
  </section>
</body>
</html>
```